Verodex business card

Business card for sustainable investment company called "Verodex". Verodex is an exchange platform selling carbon credits between buyers and sellers. Carbon Credits are an environmental commodity for reducing global carbon emissions.

the card should obviously have our logo and the theme should be sustainability/environment mixed with a trading platform.

Contact Information for Business Card

Logo, Name, Title, Phone, Email

Colors
0054AA
0677BA
7BADD7
CADEEF
E8F1F8
0094D4
00A9DD
6FCCEA
C7EBF8
E9F6FB
00AB8E
00BBA5
67D7C9
C6EFE9
E9F9F6
59FF00
82FF00
B8FF75
E3FFCB
F4FFEA

```html
<!DOCTYPE html>
<html lang="en">
<head>
<meta charset="utf-8">
<title>Verodex business card</title>
<link rel="stylesheet" href="https://fonts.googleapis.com/css2?family=Montserrat:wght@600;700&family=Open+Sans:wght@400;600&display=swap">
<style>
  :root {
    --backdrop: #1c1c1d;
    --kraft: #c9a27b;
    --kraft-dark: #bf9670;
    --ink: #1a1f26;
    --brand-navy: #0054AA;
    --brand-blue: #0677BA;
    --brand-sky: #00A9DD;
    --brand-teal: #00AB8E;
    --brand-lime: #82FF00;
  }
  * { box-sizing: border-box; margin: 0; padding: 0; }
  html, body {
    width: 1200px;
    height: 900px;
    overflow: hidden;
    background: var(--backdrop);
  }
  .stage {
    position: relative;
    width: 1200px;
    height: 900px;
  }
  .card {
    position: absolute;
    left: 320px;
    width: 560px;
    height: 320px;
    overflow: hidden;
    background: radial-gradient(circle at 40% 35%, var(--kraft) 0%, var(--kraft-dark) 100%);
    color: var(--ink);
    display: flex;
    flex-direction: column;
    align-items: center;
    justify-content: center;
  }
  .card::after {
    content: "";
    position: absolute;
    left: 0;
    right: 0;
    bottom: 0;
    height: 8px;
    background: linear-gradient(90deg, var(--brand-lime) 0%, var(--brand-teal) 35%, var(--brand-sky) 70%, var(--brand-navy) 100%);
  }
  .card--front { top: 110px; }
  .card--back { top: 470px; }

  .brand {
    display: flex;
    align-items: center;
    gap: 16px;
    font-family: "Montserrat", sans-serif;
    font-weight: 700;
    letter-spacing: 0.02em;
    color: var(--brand-navy);
  }
  .brand__mark {
    width: 30px;
    height: 30px;
    background: var(--brand-teal);
  }
  .card--front .brand__name { font-size: 44px; }
  .card--back .brand { margin-bottom: 20px; }
  .card--back .brand__mark { width: 22px; height: 22px; }
  .card--back .brand__name { font-size: 28px; }

  .person__name {
    font-family: "Montserrat", sans-serif;
    font-weight: 700;
    font-size: 19px;
    letter-spacing: 0.04em;
    text-transform: uppercase;
    text-align: center;
    color: var(--ink);
  }
  .person__title {
    font-family: "Open Sans", sans-serif;
    font-size: 14px;
    text-align: center;
    margin-top: 2px;
    color: var(--brand-blue);
  }
  .divider {
    width: 130px;
    height: 2px;
    background: linear-gradient(90deg, var(--brand-teal), var(--brand-sky));
    margin: 12px 0;
  }
  .contact {
    list-style: none;
    font-family: "Open Sans", sans-serif;
    font-size: 15px;
    line-height: 1.4;
    text-align: left;
  }
  .contact__label {
    font-weight: 600;
    color: var(--brand-blue);
  }
</style>
</head>
<body>
  <main class="stage">
    <section class="card card--front">
      <div class="brand">
        <span class="brand__mark"></span>
        <span class="brand__name">VERODEX</span>
      </div>
    </section>

    <section class="card card--back">
      <div class="brand">
        <span class="brand__mark"></span>
        <span class="brand__name">VERODEX</span>
      </div>
      <h1 class="person__name">Daniel Hartley</h1>
      <p class="person__title">Managing Director</p>
      <div class="divider"></div>
      <ul class="contact">
        <li><span class="contact__label">M:</span> 044-987 650 321</li>
        <li><span class="contact__label">E:</span> hello@verodexmail.com</li>
        <li><span class="contact__label">W:</span> www.verodexmarkets.com</li>
      </ul>
    </section>
  </main>
</body>
</html>
```